Business Card Design for a Software Startup

We'd like to have a business card design. We already have a logo. Basically what we need is a clean design with name, address, cellphone and phone numbers, e-mail and web site address (front) and a space on the back with our logo with the company name on the right side and some texts on the bottom.
We are a development and consulting company in Brazil with highly qualified team of professionals in Java, iOS and Android development and consulting.

Target Market(s)

CIO, IT managers of mid to big size companies

Industry/Entity Type

Business

```html
<!DOCTYPE html>
<html lang="en">
<head>
<meta charset="utf-8">
<title>Veltora Business Card</title>
<link href="https://fonts.googleapis.com/css2?family=Arimo:wght@400;700&display=swap" rel="stylesheet">
<style>
  :root {
    --page-bg: #e9e9ee;
    --card-white: #ffffff;
    --navy: #0b3a66;
    --navy-deep: #082c52;
    --blue: #0a4f82;
    --blue-light: #1a6aa3;
    --text-dark: #3a3a3a;
    --rule: #7f9bbd;
  }
  html, body {
    margin: 0;
    padding: 0;
    width: 1200px;
    height: 987px;
    overflow: hidden;
    background: var(--page-bg);
    font-family: "Arimo", Arial, sans-serif;
  }
  .canvas {
    position: relative;
    width: 1200px;
    height: 987px;
  }
  .card {
    position: absolute;
    left: 250px;
    width: 700px;
    height: 400px;
    border-radius: 30px;
    overflow: hidden;
    box-shadow: 0 6px 18px rgba(0,0,0,0.12);
  }
  /* Front */
  .card-front {
    top: 50px;
    background: var(--card-white);
  }
  .brand {
    position: absolute;
    left: 60px;
    top: 62px;
    display: flex;
    align-items: center;
    gap: 22px;
  }
  .brand-square {
    width: 70px;
    height: 70px;
    border-radius: 10px;
    background: var(--blue-light);
  }
  .brand-name {
    font-weight: 700;
    font-size: 84px;
    letter-spacing: 2px;
    color: var(--navy);
    line-height: 1;
  }
  .contact-band {
    position: absolute;
    left: 0;
    top: 200px;
    width: 100%;
    height: 130px;
    background: linear-gradient(90deg, var(--navy-deep), var(--blue));
    display: flex;
    align-items: center;
    color: #fff;
  }
  .identity {
    width: 270px;
    text-align: right;
    padding-right: 24px;
    box-sizing: border-box;
  }
  .identity .person-name {
    font-weight: 700;
    font-size: 26px;
  }
  .identity .person-title {
    font-size: 17px;
    margin-top: 2px;
  }
  .band-rule {
    width: 1px;
    height: 92px;
    background: var(--rule);
  }
  .contact-list {
    list-style: none;
    margin: 0;
    padding: 0 0 0 24px;
    font-size: 19px;
    line-height: 1.3;
  }
  .address {
    position: absolute;
    left: 0;
    top: 346px;
    width: 100%;
    text-align: center;
    font-size: 18px;
    color: var(--text-dark);
  }
  /* Back */
  .card-back {
    top: 530px;
    background: radial-gradient(ellipse at 60% 40%, var(--blue-light), var(--blue) 55%, var(--navy-deep));
    color: #fff;
    text-align: center;
  }
  .back-name {
    margin-top: 128px;
    font-weight: 700;
    font-size: 104px;
    letter-spacing: 3px;
    line-height: 1;
  }
  .back-web {
    margin-top: 34px;
    font-weight: 700;
    font-size: 22px;
    letter-spacing: 8px;
  }
</style>
</head>
<body>
<main class="canvas">
  <section class="card card-front" aria-label="Card front">
    <div class="brand">
      <div class="brand-square"></div>
      <div class="brand-name">VELTORA</div>
    </div>
    <div class="contact-band">
      <div class="identity">
        <div class="person-name">Your Name</div>
        <div class="person-title">Title</div>
      </div>
      <div class="band-rule"></div>
      <ul class="contact-list">
        <li>p: 123-456-7890</li>
        <li>c: 123-456-7890</li>
        <li>e: yourname@veltora.com</li>
        <li>w: www.veltora.com</li>
      </ul>
    </div>
    <div class="address">Door No. Street Name City Name, State, Zip Code.</div>
  </section>

  <section class="card card-back" aria-label="Card back">
    <div class="back-name">VELTORA</div>
    <div class="back-web">www.veltora.com</div>
  </section>
</main>
</body>
</html>
```